Create modern and sleek business card for luxury real estate company

We're a "boutique" real estate office looking for a design that gets across a highly modern luxury brand. Blacks and whites are probably the best colors unless we try a silver foil for the logo. I've attached a version of our current logo here. I'd like to swap out the current font on there with Gotham Light Regular.

I'm looking to have one side of the card have the logo with the space for our agents info on the other side.

Target Market(s)

Young professionals in a "luxury" headspace

Industry/Entity Type

Real estate

Contact Information for Business Card

A place for agent name, cell number, website. The slogan "Simply Rethinking Real Estate".

Font styles to use
Other font styles liked:
• Gotham Regular

Colors

Designer to choose only greyscale colors for use in the design.

Requirements
Must have
• Matte black as the background color. Clean lines and use of contrast. A specific design aspect that will use silver foil.
Nice to have
• Up in the air on integrating a QR code
Should not have
• Any houses or other real estate related design (ex: a clip art house)

```html
<!DOCTYPE html>
<html lang="en">
<head>
<meta charset="utf-8">
<title>Meridian Estates — Business Card</title>
<link href="https://fonts.googleapis.com/css2?family=Montserrat:wght@300;400;600&display=swap" rel="stylesheet">
<style>
  :root {
    --page: #e9e9ea;
    --matte-black: #050505;
    --paper: #f7f7f7;
    --ink: #111111;
    --silver: #d6d6d6;
    --silver-dark: #6e6e6e;
    --shadow: rgba(0, 0, 0, 0.35);
  }
  * { margin: 0; padding: 0; box-sizing: border-box; }
  html, body {
    width: 1200px;
    height: 1200px;
    overflow: hidden;
    background: var(--page);
    font-family: "Montserrat", sans-serif;
  }
  .sheet {
    width: 1200px;
    height: 1200px;
    display: flex;
    flex-direction: column;
    align-items: center;
    justify-content: center;
    gap: 56px;
  }
  .card {
    position: relative;
    width: 900px;
    height: 514px;
    overflow: hidden;
    background: var(--matte-black);
    box-shadow: 0 14px 30px var(--shadow);
  }
  .card svg.card-art {
    position: absolute;
    inset: 0;
    width: 100%;
    height: 100%;
  }
  .brand {
    position: absolute;
    display: flex;
    align-items: center;
    gap: 18px;
    color: var(--silver);
  }
  .brand-dot {
    width: 62px;
    height: 62px;
    border: 2px solid var(--silver);
    border-radius: 50%;
  }
  .brand-name {
    display: flex;
    flex-direction: column;
    font-weight: 400;
    font-size: 30px;
    letter-spacing: 3px;
    line-height: 1.15;
    text-transform: uppercase;
  }
  .brand-name .rule {
    display: block;
    height: 2px;
    background: var(--silver);
    margin: 3px 0;
  }
  .brand-name .second { padding-left: 20px; }
  .front .brand { left: 70px; top: 210px; }
  .back .brand { left: 50%; top: 50%; transform: translate(-50%, -50%); }

  .agent {
    position: absolute;
    left: 555px;
    top: 178px;
    right: 0;
    color: var(--ink);
  }
  .agent-name {
    font-weight: 600;
    font-size: 26px;
    letter-spacing: 1px;
    text-transform: uppercase;
  }
  .agent-title {
    font-weight: 400;
    font-size: 17px;
    letter-spacing: 1px;
    text-transform: uppercase;
    margin-top: 2px;
  }
  .agent-rule {
    height: 4px;
    background: var(--ink);
    margin: 10px 0 14px;
  }
  .contact-line {
    display: flex;
    align-items: center;
    gap: 12px;
    font-weight: 400;
    font-size: 18px;
    margin-bottom: 10px;
  }
  .contact-line svg { width: 18px; height: 18px; flex: none; }
</style>
</head>
<body>
<main class="sheet">

  <section class="card front" aria-label="Card front">
    <svg class="card-art" viewBox="0 0 900 514" aria-hidden="true">
      <defs>
        <linearGradient id="silverArc" x1="0" y1="0" x2="0" y2="1">
          <stop offset="0" stop-color="#9a9a9a"/>
          <stop offset="0.5" stop-color="#e2e2e2"/>
          <stop offset="1" stop-color="#5c5c5c"/>
        </linearGradient>
      </defs>
      <rect width="900" height="514" fill="var(--paper)"/>
      <circle cx="58" cy="257" r="432" fill="#d0d0d0"/>
      <circle cx="58" cy="257" r="424" fill="url(#silverArc)"/>
      <circle cx="58" cy="257" r="412" fill="var(--matte-black)"/>
    </svg>

    <div class="brand">
      <span class="brand-dot"></span>
      <span class="brand-name">
        <span>Meridian</span>
        <span class="rule"></span>
        <span class="second">Estates</span>
      </span>
    </div>

    <div class="agent">
      <p class="agent-name">Alex Morgan</p>
      <p class="agent-title">Designer</p>
      <div class="agent-rule"></div>
      <p class="contact-line">
        <svg viewBox="0 0 24 24"><path fill="#111" d="M6.6 10.8a15.1 15.1 0 0 0 6.6 6.6l2.2-2.2c.3-.3.7-.4 1-.2 1.1.4 2.3.6 3.6.6.6 0 1 .4 1 1V20c0 .6-.4 1-1 1A17 17 0 0 1 3 4c0-.6.4-1 1-1h3.5c.6 0 1 .4 1 1 0 1.3.2 2.5.6 3.6.1.3 0 .7-.2 1z"/></svg>
        012-555-0147
      </p>
      <p class="contact-line">
        <svg viewBox="0 0 24 24"><circle cx="12" cy="12" r="10" fill="#111"/><path fill="none" stroke="#f7f7f7" stroke-width="1.5" d="M2 12h20M12 2c3 3 3 17 0 20M12 2c-3 3-3 17 0 20"/></svg>
        www.meridianestates.com
      </p>
    </div>
  </section>

  <section class="card back" aria-label="Card back">
    <svg class="card-art" viewBox="0 0 900 514" aria-hidden="true">
      <defs>
        <linearGradient id="silverRing" x1="0" y1="0" x2="1" y2="1">
          <stop offset="0" stop-color="#5a5a5a"/>
          <stop offset="0.45" stop-color="#c9c9c9"/>
          <stop offset="1" stop-color="#4a4a4a"/>
        </linearGradient>
      </defs>
      <rect width="900" height="514" fill="var(--matte-black)"/>
      <ellipse cx="450" cy="257" rx="440" ry="262" fill="url(#silverRing)"/>
      <ellipse cx="450" cy="257" rx="418" ry="244" fill="var(--matte-black)"/>
    </svg>

    <div class="brand">
      <span class="brand-dot"></span>
      <span class="brand-name">
        <span>Meridian</span>
        <span class="rule"></span>
        <span class="second">Estates</span>
      </span>
    </div>
  </section>

</main>
</body>
</html>
```